Roofing Contractor business card redesign

I want to redesign my business card with a fresh, eye catching concept

Target Market(s)

Residential Roofing Clients, potential employees, and subcontractors.

Industry/Entity Type

Business

Colors

Designer to choose colors to be used in the design.

Requirements
Nice to have
• I just want something that's more pleasing to the eye. You can use a combination of either / or of my logos.

```html
<!DOCTYPE html>
<html lang="en">
<head>
<meta charset="utf-8">
<title>Bright Ridge Business Card</title>
<link rel="stylesheet" href="https://fonts.googleapis.com/css2?family=Bebas+Neue&family=Rambla:wght@400;700&display=swap">
<style>
  :root {
    --backdrop: #3b3b3b;
    --card-white: #f1f1f1;
    --brown: #4a1410;
    --orange: #e5701f;
    --orange-light: #f4b23a;
    --ink: #555555;
    --rule: #b8b8b8;
  }
  html, body {
    margin: 0;
    width: 1200px;
    height: 960px;
    overflow: hidden;
    background: var(--backdrop);
  }
  .canvas { position: relative; width: 1200px; height: 960px; }

  .card { position: absolute; width: 600px; height: 343px; box-shadow: 0 3px 6px rgba(0,0,0,.45); }

  .card-front { left: 320px; top: 103px; background: linear-gradient(135deg, #e4e4e4, var(--card-white) 45%, #f7f7f7); }
  .identity { position: absolute; right: 330px; top: 122px; text-align: right; }
  .identity-name {
    margin: 0; font-family: "Bebas Neue", sans-serif; font-weight: 400;
    font-size: 34px; line-height: 30px; color: var(--brown); letter-spacing: .5px;
  }
  .identity-role {
    margin: 4px 0 0; font-family: "Rambla", sans-serif; font-size: 14.5px;
    line-height: 18px; color: var(--orange);
  }
  .divider { position: absolute; left: 292px; top: 109px; width: 1px; height: 104px; background: var(--rule); }
  .contact {
    position: absolute; left: 315px; top: 108px; margin: 0;
    font-family: "Rambla", sans-serif; font-size: 14.5px; line-height: 18px; color: var(--ink);
    font-style: normal;
  }
  .contact-address { margin: 0 0 8px; }
  .contact-line { display: flex; align-items: center; gap: 8px; margin: 0 0 1px; }
  .contact-line svg { width: 13px; height: 13px; flex: none; }

  .band { position: absolute; left: 0; top: 288px; width: 600px; height: 30px; display: flex; }
  .band-web {
    flex: 0 0 525px; background: var(--orange); color: #fff;
    font-family: "Rambla", sans-serif; font-size: 14.5px; letter-spacing: 3px;
    line-height: 30px; text-align: center; box-sizing: border-box; padding-right: 60px;
  }
  .band-end { flex: 1; background: var(--brown); }
  .band-mark {
    position: absolute; left: 493px; top: -1px; width: 30px; height: 30px;
    border-radius: 50%; background: var(--brown); border: 2px solid #fff; box-sizing: border-box;
  }

  .card-back {
    left: 317px; top: 488px;
    background: linear-gradient(135deg, var(--orange-light) 0%, var(--orange) 32%, var(--orange) 100%);
  }
  .brand {
    position: absolute; left: 0; right: 0; top: 98px; text-align: center;
    font-family: "Bebas Neue", sans-serif; font-weight: 400; color: var(--brown);
  }
  .brand-row { display: flex; align-items: center; justify-content: center; gap: 14px; }
  .brand-dot { width: 74px; height: 74px; border-radius: 50%; background: var(--brown); }
  .brand-name { margin: 0; font-size: 84px; line-height: 78px; letter-spacing: 1px; }
  .brand-sub { margin: 6px 0 0; font-size: 34px; line-height: 34px; letter-spacing: 1px; }
</style>
</head>
<body>
<main class="canvas">
  <section class="card card-front">
    <div class="identity">
      <h1 class="identity-name">Sam Calloway</h1>
      <p class="identity-role">Stratton Certified Roof Inspector<br>Licensed Property Adjuster</p>
    </div>
    <div class="divider"></div>
    <address class="contact">
      <p class="contact-address">4815 Ridgeline Avenue Suite 210<br>Fairview, TX 75069</p>
      <p class="contact-line">
        <svg viewBox="0 0 16 16" aria-hidden="true"><path fill="#4a1410" d="M3.6 1.2l2.3 2.9-1.4 1.8c.9 2 2.6 3.7 4.6 4.6l1.8-1.4 2.9 2.3-1.3 2.6C7 13.7 2.3 9 1 3.5z"/></svg>
        (555) 218-4400
      </p>
      <p class="contact-line">
        <svg viewBox="0 0 16 16" aria-hidden="true"><rect x="3.5" y="0.5" width="9" height="15" rx="1.5" fill="#4a1410"/><rect x="5" y="2.5" width="6" height="9.5" fill="#f1f1f1"/></svg>
        (555) 307-6182
      </p>
      <p class="contact-line">
        <svg viewBox="0 0 16 16" aria-hidden="true"><rect x="1" y="3.5" width="14" height="9.5" fill="#4a1410"/><path d="M1.5 4l6.5 5 6.5-5" fill="none" stroke="#f1f1f1" stroke-width="1.2"/></svg>
        sam@brightridgetx.com
      </p>
    </address>
    <div class="band">
      <div class="band-web">www.brightridgetx.com</div>
      <div class="band-end"></div>
      <div class="band-mark"></div>
    </div>
  </section>

  <section class="card card-back">
    <div class="brand">
      <div class="brand-row">
        <div class="brand-dot"></div>
        <p class="brand-name">Bright Ridge</p>
      </div>
      <p class="brand-sub">General Contractors, Inc.</p>
    </div>
  </section>
</main>
</body>
</html>
```